HARBORLINE AUTO GLASS

Mobile Glass Shop:

1) Windshield REPAIR 2)Windshield replacment 3) Rear Windshield Replacment 4) Side Window Replacment 5) car window replacment 6) Power Window Repair.

Schedual a service within 24 hour with one of our certified technicians.
Updates

See "brightvane auto repair" web site for referance on the nature of our buisness and service. www.brightvane-example.com

Coding

```html
<!DOCTYPE html>
<html lang="en">
<head>
<meta charset="utf-8">
<title>Harborline Auto Glass</title>
<link rel="stylesheet" href="https://fonts.googleapis.com/css2?family=Roboto+Condensed:wght@300;400;700&family=Roboto:wght@400;500;700&family=Poppins:wght@600&display=swap">
<style>
:root{
  --blue:#1a8fd6;
  --blue-deep:#2b7cb9;
  --blue-bright:#0a98e2;
  --ink:#222428;
  --text:#333;
  --hero-bg:#f1f1f1;
  --dark:#1c1d21;
  --white:#fff;
}
*{margin:0;padding:0;box-sizing:border-box}
html,body{width:1200px;height:3696px;overflow:hidden}
body{position:relative;background:var(--white);font-family:"Roboto",sans-serif;color:var(--text)}
.abs{position:absolute}
.heading{font-family:"Roboto Condensed",sans-serif;font-weight:700;color:var(--ink)}

/* header */
.logo{left:112px;top:30px;display:flex;align-items:center;gap:12px;font-family:"Roboto Condensed",sans-serif;font-weight:700;font-size:30px;color:var(--blue);letter-spacing:.5px}
.logo-mark{width:34px;height:34px;background:var(--blue);border-radius:4px}
.nav{left:478px;top:39px;font-size:14px;font-weight:500;color:var(--ink)}
.nav a{color:inherit;text-decoration:none;position:absolute;white-space:nowrap}
.nav a.active{color:var(--blue)}
.btn{display:inline-flex;align-items:center;justify-content:center;background:var(--blue);color:var(--white);border-radius:24px;font-weight:700;font-size:14px;box-shadow:0 4px 8px rgba(0,0,0,.15);white-space:nowrap}
.quote{left:959px;top:29px;width:129px;height:40px}

/* hero */
.hero-title{left:110px;top:276px;font-size:69px;line-height:68px}
.start{left:110px;top:428px;width:143px;height:41px}
.dots{left:110px;top:612px;display:flex;gap:8px}
.dots i{width:12px;height:12px;border-radius:50%;background:#cfcfcf}
.dots i:first-child{background:var(--blue)}

/* services */
.section-title{left:0;width:1200px;text-align:center;font-size:43px}
.card{width:309px;height:379px;background:var(--white);box-shadow:0 2px 10px rgba(0,0,0,.08);overflow:hidden}
.card .photo{position:absolute;left:19px;top:19px;width:270px;height:268px;border-radius:10px 0 70px 0}
.card h3{position:absolute;left:0;width:309px;top:312px;text-align:center;font-family:"Roboto",sans-serif;font-weight:500;font-size:22px;line-height:26px;color:var(--ink)}
.card .go{position:absolute;right:-28px;bottom:-30px;width:86px;height:86px;border-radius:50%;background:var(--blue)}
.card .go svg{position:absolute;left:20px;top:18px}

/* about */
.about-photo{left:165px;top:1870px;width:396px;height:396px;border-radius:50%;border:5px solid var(--white);background:radial-gradient(circle at 40% 40%,#9aa4ad,#3f464d 70%)}
.about-title{left:617px;top:1868px;font-size:43px;color:var(--white)}
.about-text{left:617px;top:1936px;width:471px;font-size:14.5px;line-height:25.8px;color:var(--white);text-align:justify}
.about-text p+p{margin-top:25px}
.learn{left:617px;top:2220px;width:142px;height:41px;background:var(--white);color:var(--blue);font-size:13px}

/* blog */
.post{width:309px;height:416px;background:var(--blue);color:var(--white);text-align:center}
.post.alt{background:var(--blue-deep)}
.post .photo{position:absolute;left:7px;top:7px;width:295px;height:208px}
.post h3{position:absolute;top:244px;width:100%;font-family:"Roboto Condensed",sans-serif;font-weight:700;font-size:23px}
.post .date{position:absolute;top:282px;width:100%;font-size:14px;text-decoration:underline}
.post p{position:absolute;top:312px;left:30px;right:30px;font-size:14px;line-height:26px}

/* newsletter */
.news{left:112px;top:3083px;width:976px;height:196px;background:linear-gradient(90deg,#1b8fd8,#2a7bbd)}
.news h2{position:absolute;left:50px;top:34px;font-family:"Roboto Condensed",sans-serif;color:var(--white);font-size:52px;line-height:64px;font-weight:300;white-space:nowrap}
.news h2 b{font-weight:700}
.news .field{position:absolute;left:418px;top:65px;width:519px;height:68px;background:var(--white);display:flex;align-items:center;padding-left:20px;font-size:14px;color:#666;gap:6px}
.news .field svg.send{position:absolute;right:30px;top:22px}

/* footer */
.touch{left:0;width:1200px;top:3352px;text-align:center;font-family:"Poppins",sans-serif;font-weight:600;font-size:20px;color:var(--white)}
.contact{width:300px;text-align:center;color:var(--white)}
.contact .icon{width:58px;height:58px;margin:0 auto;border-radius:50%;background:var(--blue);display:flex;align-items:center;justify-content:center}
.contact h4{margin-top:22px;font-size:17px;font-weight:700}
.contact span{display:block;margin-top:16px;font-size:14.5px;white-space:nowrap}
.divider{width:1px;height:174px;top:3416px;background:#888}
.copy{left:0;width:1200px;top:3651px;text-align:center;font-size:13px;color:var(--white)}
</style>
</head>
<body>

<!-- hero backdrop -->
<svg class="abs" style="left:0;top:0" width="1200" height="720" aria-hidden="true">
  <polygon points="0,0 1200,0 1200,660 0,706" fill="var(--hero-bg)"/>
  <polygon points="563,86 1200,75 1200,631 600,706" fill="var(--blue)"/>
</svg>
<div class="abs" role="img" aria-label="Technician repairing a car windshield with a tool" style="left:600px;top:106px;width:600px;height:600px;background:linear-gradient(135deg,#c9cdd1,#6b7580 55%,#2e3338);clip-path:polygon(0 0,100% 0,100% 87.5%,0 100%)"></div>

<header>
  <div class="abs logo"><span class="logo-mark"></span>HARBORLINE</div>
  <nav class="abs nav">
    <a class="active" style="left:0">Home</a>
    <a style="left:65px">About us</a>
    <a style="left:149px">Services</a>
    <a style="left:231px">Blog</a>
    <a style="left:286px">Locations</a>
    <a style="left:376px">Contact us</a>
  </nav>
  <a class="abs btn quote">GET A QUOTE</a>
</header>

<h1 class="abs heading hero-title">HARBORLINE<br>AUTO GLASS</h1>
<a class="abs btn start">GET STARTED</a>
<div class="abs dots"><i></i><i></i><i></i><i></i></div>

<!-- services -->
<h2 class="abs heading section-title" style="top:762px">OUR SERVICES</h2>

<svg width="0" height="0" style="position:absolute"><defs>
  <symbol id="chev" viewBox="0 0 20 20"><path d="M4 5l5 5-5 5M10 5l5 5-5 5" fill="none" stroke="#fff" stroke-width="2.2"/></symbol>
</defs></svg>

<div class="abs card" style="left:112px;top:847px"><div class="photo" role="img" aria-label="Technician fitting a windshield" style="background:linear-gradient(135deg,#9ea3a6,#5d6266)"></div><h3>Windshield<br>REPAIR</h3><span class="go"><svg width="16" height="16"><use href="#chev"/></svg></span></div>
<div class="abs card" style="left:446px;top:847px"><div class="photo" role="img" aria-label="Technician inspecting windshield glass" style="background:linear-gradient(135deg,#3a69b8,#1d2e50)"></div><h3>Windshield<br>replacment</h3><span class="go"><svg width="16" height="16"><use href="#chev"/></svg></span></div>
<div class="abs card" style="left:779px;top:847px"><div class="photo" role="img" aria-label="Glass repair tool on a windshield" style="background:linear-gradient(135deg,#8a8f94,#c0c4c7)"></div><h3>Rear Windshield<br>Replacment</h3><span class="go"><svg width="16" height="16"><use href="#chev"/></svg></span></div>
<div class="abs card" style="left:112px;top:1250px"><div class="photo" role="img" aria-label="Technician cleaning a side window" style="background:linear-gradient(135deg,#2a5f95,#8c99a6)"></div><h3>Side Window<br>Replacment</h3><span class="go"><svg width="16" height="16"><use href="#chev"/></svg></span></div>
<div class="abs card" style="left:446px;top:1250px"><div class="photo" role="img" aria-label="Hands fitting a car door window" style="background:linear-gradient(135deg,#4d5a66,#c8ccd0)"></div><h3>Car Window<br>Replacment</h3><span class="go"><svg width="16" height="16"><use href="#chev"/></svg></span></div>
<div class="abs card" style="left:779px;top:1250px"><div class="photo" role="img" aria-label="Resin injector tool on glass" style="background:linear-gradient(135deg,#9aa1a7,#2f3438)"></div><h3>Power Window<br>Repair</h3><span class="go"><svg width="16" height="16"><use href="#chev"/></svg></span></div>

<!-- about -->
<svg class="abs" style="left:0;top:1730px" width="1200" height="700" aria-hidden="true">
  <defs><linearGradient id="aboutBg" x1="0" y1="0" x2="1" y2="1"><stop offset="0" stop-color="#0a8edb"/><stop offset="1" stop-color="#0a98e2"/></linearGradient></defs>
  <polygon points="0,86 1200,4 1200,695 0,610" fill="url(#aboutBg)"/>
</svg>
<div class="abs about-photo" role="img" aria-label="Hand holding a windshield repair injector"></div>
<h2 class="abs heading about-title">ABOUT US</h2>
<div class="abs about-text">
  <p>Lorem ipsum dolor sit amet, consectetur adipiscing elit, sed do eiusmod tempor incididunt ut labore et dolore magna aliqua. Ut enim ad minim veniam, quis nostrud exercitation ullamco laboris nisi ut aliquip ex ea commodo consequat. Duis aute irure dolor in reprehenderit in voluptate velit esse cillum dolore eu fugiat nulla pariatur.</p>
  <p>Excepteur sint occaecat cupidatat non proident, sunt in culpa qui officia deserunt mollit anim id est laborum. Lorem ipsum dolor sit amet, consectetur adipiscing elit, sed do eiusmod tempor incididunt ut labore et dolore magna aliqua.</p>
</div>
<a class="abs btn learn">LEARN MORE &#10148;</a>

<!-- blog -->
<h2 class="abs heading section-title" style="top:2472px">OUR LATEST BLOG</h2>
<div class="abs post" style="left:112px;top:2555px"><div class="photo" role="img" aria-label="Technician working on a dark car windshield" style="background:linear-gradient(135deg,#e9e9ea,#3a3f47 60%,#1c1f24)"></div><h3>DUIS AUTE IRURE DOLOR</h3><div class="date">Jan 20, 2022</div><p>Lorem ipsum dolor sit amet, conse ctetur adipiscing elit, sed do eiusmod tempor incididunt</p></div>
<div class="abs post alt" style="left:446px;top:2555px"><div class="photo" role="img" aria-label="Hands using a tool on glass" style="background:linear-gradient(135deg,#2d3d5a,#c9b3a4 55%,#3a4452)"></div><h3>DUIS AUTE IRURE DOLOR</h3><div class="date">Jan 20, 2022</div><p>Lorem ipsum dolor sit amet, conse ctetur adipiscing elit, sed do eiusmod tempor incididunt</p></div>
<div class="abs post" style="left:779px;top:2555px"><div class="photo" role="img" aria-label="Technician lifting a windshield with suction cups" style="background:linear-gradient(135deg,#6a7077,#23262b 60%,#bfb6a8)"></div><h3>DUIS AUTE IRURE DOLOR</h3><div class="date">Jan 20, 2022</div><p>Lorem ipsum dolor sit amet, conse ctetur adipiscing elit, sed do eiusmod tempor incididunt</p></div>

<!-- footer -->
<svg class="abs" style="left:0;top:3110px" width="1200" height="586" aria-hidden="true">
  <polygon points="0,5 1200,112 1200,586 0,586" fill="var(--dark)"/>
</svg>

<section class="abs news">
  <h2>SUBSCRIBE OUR<br><b>NEWSLETTER</b></h2>
  <div class="field">
    <svg width="13" height="10" viewBox="0 0 13 10"><rect width="13" height="10" fill="#666"/><path d="M0 0l6.5 5L13 0" stroke="#fff" fill="none"/></svg>Email Address
    <svg class="send" width="26" height="24" viewBox="0 0 26 24"><path d="M0 11L26 0 21 24 13 16 10 22 9 14z" fill="#1a8fd6"/></svg>
  </div>
</section>

<h3 class="abs touch">GET IN TOUCH</h3>
<div class="abs contact" style="left:123px;top:3429px">
  <div class="icon"><svg width="14" height="20" viewBox="0 0 14 20"><path d="M7 0a7 7 0 0 1 7 7c0 5-7 13-7 13S0 12 0 7a7 7 0 0 1 7-7z" fill="#fff"/><circle cx="7" cy="7" r="2.6" fill="#1a8fd6"/></svg></div>
  <h4>Address</h4><span>Lorem ipsum dolor sit amet, consec</span>
</div>
<div class="abs divider" style="left:462px"></div>
<div class="abs contact" style="left:450px;top:3429px">
  <div class="icon"><svg width="18" height="18" viewBox="0 0 24 24"><path d="M6.6 10.8a15 15 0 0 0 6.6 6.6l2.2-2.2a1 1 0 0 1 1-.25 11 11 0 0 0 3.6.6 1 1 0 0 1 1 1V20a1 1 0 0 1-1 1A17 17 0 0 1 3 4a1 1 0 0 1 1-1h3.5a1 1 0 0 1 1 1 11 11 0 0 0 .6 3.6 1 1 0 0 1-.25 1z" fill="#fff"/></svg></div>
  <h4>Phone</h4><span>+1 555 014 2290</span>
</div>
<div class="abs divider" style="left:754px"></div>
<div class="abs contact" style="left:777px;top:3429px">
  <div class="icon"><svg width="20" height="15" viewBox="0 0 20 15"><rect width="20" height="15" rx="1" fill="#fff"/><path d="M0 1l10 7 10-7" stroke="#1a8fd6" stroke-width="1.6" fill="none"/></svg></div>
  <h4>Email Address</h4><span>hello@harborline-example.com</span>
</div>

<p class="abs copy">&copy; Copyrights 2022 Harborline Auto Glass</p>

</body>
</html>
```